Laser Tattoo Removal Business Cards

We are looking for a professional business card design for a laser tattoo removal business. Ideally looking for a black business card design. The name of the business is Brightline Tattoo Removal. We place our cards at local tattoo shops so we ideally are looking for something trendy/edgy to draw both male and female clientele in.

Target Market(s)

Male/Female ages 18-60

Contact Information for Business Card

black background ideally.. hoping to stay within greys, whites and black

Font styles to use
Serif
Sans Serif

Colors
121212
a9a9a9
5c5c5c
f5f5f5
ffffff
7f7f7f
606060
848484
9d9d9d

Requirements
Must have
• Employee Info:
• Melissa Thornbury
• Chief Executive Offer
• m: 919.537.2846
• w: 919.362.4178
• f: 919.685.3907
• mthornbury@brightlinetattooremoval.example
• Address:
• 4615 Oakmere Pkwy, Suite 210
• Raleigh, NC 27654
• Website:
• www.brightlinetattooremoval.example
Nice to have
• Myabe business name on back or logo on back and employee info on the front

```html
<!DOCTYPE html>
<html lang="en">
<head>
<meta charset="utf-8">
<title>Brightline Tattoo Removal – Business Cards</title>
<link rel="stylesheet" href="https://fonts.googleapis.com/css2?family=Roboto:wght@400;500&family=Roboto+Condensed:wght@700&display=swap">
<style>
  :root {
    --ink: #121212;
    --paper: #f5f5f5;
    --white: #ffffff;
    --grey-light: #a9a9a9;
    --grey-mid: #7f7f7f;
    --grey-dark: #5c5c5c;
    --grey-text: #606060;
    --stage: #dcdcdc;
  }
  * { margin: 0; padding: 0; box-sizing: border-box; }
  html, body { width: 1200px; height: 960px; overflow: hidden; }
  body {
    background: var(--stage);
    font-family: "Roboto", Arial, sans-serif;
    position: relative;
  }
  .card {
    position: absolute;
    width: 600px;
    height: 342px;
    overflow: hidden;
  }
  /* Front */
  .card-front {
    left: 315px; top: 113px;
    background: var(--paper);
    color: var(--ink);
  }
  .wordmark {
    position: absolute;
    text-align: center;
    font-weight: 500;
    text-transform: uppercase;
    white-space: nowrap;
  }
  .card-front .wordmark {
    left: 330px; top: 52px; width: 260px;
    color: #2a2a2a;
  }
  .wordmark-name { display: block; font-size: 34px; letter-spacing: 3px; line-height: 1; }
  .wordmark-sub { display: block; font-size: 14px; letter-spacing: 3px; margin-top: 26px; }
  .holder {
    position: absolute; left: 30px; top: 168px;
  }
  .holder-name {
    font-family: "Roboto Condensed", "Arial Narrow", sans-serif;
    font-weight: 700; font-size: 21px; color: var(--ink); line-height: 1.1;
  }
  .holder-title { font-size: 15px; color: var(--grey-light); margin-top: 2px; }
  .divider {
    position: absolute; left: 30px; top: 219px; width: 536px; height: 2px;
    background: var(--grey-mid);
  }
  .contact-list {
    position: absolute; left: 30px; top: 234px; list-style: none;
    font-size: 12.5px; color: var(--grey-text); line-height: 19px;
    white-space: nowrap;
  }
  .contact-list li { display: flex; align-items: center; gap: 9px; }
  .contact-list svg { width: 12px; height: 12px; fill: var(--ink); flex: none; }
  .address {
    position: absolute; right: 33px; top: 234px; text-align: right;
    font-style: normal; font-size: 12.5px; color: var(--grey-text); line-height: 19px;
    white-space: nowrap;
  }
  /* Back */
  .card-back {
    left: 311px; top: 473px;
    background: var(--ink);
    color: var(--white);
  }
  .card-back .wordmark {
    left: 120px; top: 100px; width: 360px; color: var(--white);
  }
  .card-back .wordmark-name { font-size: 48px; letter-spacing: 4px; }
  .card-back .wordmark-sub { font-size: 18px; letter-spacing: 4px; margin-top: 32px; }
  .web-band {
    position: absolute; left: 0; top: 287px; width: 100%; height: 27px;
    background: var(--white); color: var(--ink);
    display: flex; align-items: center; justify-content: center;
    font-size: 14px; letter-spacing: 2.6px; white-space: nowrap;
  }
</style>
</head>
<body>

<section class="card card-front" aria-label="Business card front">
  <div class="wordmark">
    <span class="wordmark-name">Brightline</span>
    <span class="wordmark-sub">Tattoo Removal</span>
  </div>

  <div class="holder">
    <div class="holder-name">MELISSA THORNBURY</div>
    <div class="holder-title">Chief Executive Offer</div>
  </div>
  <div class="divider"></div>

  <ul class="contact-list">
    <li><svg viewBox="0 0 16 16" aria-label="Work phone"><path d="M3.6 1l2.6 3-1.5 1.7c.9 2 2.6 3.7 4.6 4.6L11 8.8l3 2.6-1.5 2.9C6.6 14.3 1.7 9.4 1.7 3.5z"/></svg>919.362.4178</li>
    <li><svg viewBox="0 0 16 16" aria-label="Mobile phone"><path d="M4 0h8a1 1 0 0 1 1 1v14a1 1 0 0 1-1 1H4a1 1 0 0 1-1-1V1a1 1 0 0 1 1-1zm1 2v10h6V2zm3 11a1 1 0 1 0 0 2 1 1 0 0 0 0-2z"/></svg>919.537.2846</li>
    <li><svg viewBox="0 0 16 16" aria-label="Fax"><path d="M4 1h8v4H4zM1 6h14v7h-3v2H4v-2H1zm4 5v3h6v-3z"/></svg>919.685.3907</li>
    <li><svg viewBox="0 0 16 16" aria-label="Email"><path d="M1 3h14v1.5L8 9 1 4.5zm0 3.2l7 4.5 7-4.5V13H1z"/></svg>mthornbury@brightlinetattooremoval.example</li>
  </ul>

  <address class="address">
    4615 Oakmere Pkwy<br>
    Suite 210<br>
    Raleigh, NC 27654<br>
    www.brightlinetattooremoval.example
  </address>
</section>

<section class="card card-back" aria-label="Business card back">
  <div class="wordmark">
    <span class="wordmark-name">Brightline</span>
    <span class="wordmark-sub">Tattoo Removal</span>
  </div>
  <div class="web-band">www.brightlinetattooremoval.example</div>
</section>

</body>
</html>
```